Business card for medical clinic

I need an upmarket, modern medical/health business card for my clinic

Contact Information for Business Card

name, address, email, qr code

```html
<!DOCTYPE html>
<html lang="en">
<head>
<meta charset="utf-8">
<title>Calder Health Partners – Business Card</title>
<link href="https://fonts.googleapis.com/css2?family=Montserrat:wght@400;500;700&display=swap" rel="stylesheet">
<style>
  :root {
    --page-bg: #e9e6e1;
    --front-bg: #1f2940;
    --front-shadow: rgba(0, 0, 0, 0.35);
    --accent-sky: #29a8e0;
    --brand-blue: #2f79b4;
    --text-light: #e8ecf3;
    --back-light: #0a92c8;
    --back-dark: #0a4c6c;
    --white: #ffffff;
  }
  * { margin: 0; padding: 0; box-sizing: border-box; }
  html, body {
    width: 900px; height: 1200px; overflow: hidden;
    background: var(--page-bg);
    font-family: "Montserrat", Arial, sans-serif;
  }
  .canvas { position: relative; width: 900px; height: 1200px; }

  .card {
    position: absolute;
    border-radius: 24px;
    overflow: hidden;
    box-shadow: 0 8px 20px var(--front-shadow);
  }

  /* Front */
  .card-front {
    left: 80px; top: 130px; width: 742px; height: 442px;
    background: var(--front-bg);
  }
  .front-band {
    position: absolute; left: 0; right: 0; bottom: 0; height: 16px;
    background: var(--accent-sky);
  }
  .front-brand {
    position: absolute; left: 35px; top: 70px;
    font-size: 22px; font-weight: 500; letter-spacing: 1.5px;
    text-transform: uppercase;
    color: var(--brand-blue);
  }
  .person-name {
    position: absolute; left: 38px; top: 185px;
    font-size: 24px; font-weight: 700; color: var(--accent-sky);
  }
  .person-title {
    position: absolute; left: 38px; top: 218px;
    font-size: 15px; font-weight: 400; color: var(--text-light);
  }
  .address {
    position: absolute; left: 40px; top: 262px;
    font-size: 16px; line-height: 21px; color: var(--text-light);
    font-style: normal;
  }
  .contact-list { position: absolute; left: 40px; top: 324px; list-style: none; }
  .contact-item {
    display: flex; align-items: center; gap: 11px;
    height: 31px;
    font-size: 15px; color: var(--text-light);
  }
  .contact-icon { width: 16px; height: 16px; flex: none; }

  /* Back */
  .card-back {
    left: 78px; top: 638px; width: 744px; height: 440px;
    background: linear-gradient(35deg, var(--back-light) 0%, #087ba9 45%, var(--back-dark) 100%);
  }
  .back-brand {
    position: absolute; left: 0; right: 0; top: 0; bottom: 0;
    display: flex; align-items: center; justify-content: center; gap: 22px;
  }
  .back-ring {
    width: 96px; height: 96px; border-radius: 50%;
    border: 5px solid var(--white);
  }
  .back-name {
    font-size: 30px; font-weight: 500; letter-spacing: 2px;
    text-transform: uppercase; color: var(--white);
  }
</style>
</head>
<body>
<main class="canvas">
  <section class="card card-front" aria-label="Card front">
    <div class="front-brand">Calder Health Partners</div>
    <h1 class="person-name">Daniel Rowe</h1>
    <p class="person-title">Managing Director</p>
    <address class="address">240 Cedar Ridge Road<br>Fairview, OR 97024</address>
    <ul class="contact-list">
      <li class="contact-item">
        <svg class="contact-icon" viewBox="0 0 16 16" aria-hidden="true">
          <path fill="#29a8e0" d="M3.2 1.5l2.3 2.9-1.3 1.6c.9 2 2.4 3.5 4.4 4.4l1.6-1.3 2.9 2.3-1.4 2.3C6.5 13.6 2.4 9.5 1 3.4z"/>
          <path fill="none" stroke="#29a8e0" stroke-width="1.1" d="M9.5 1.5a5 5 0 0 1 5 5M9.5 4a2.5 2.5 0 0 1 2.5 2.5"/>
        </svg>
        <span>555.013.2740</span>
      </li>
      <li class="contact-item">
        <svg class="contact-icon" viewBox="0 0 16 16" aria-hidden="true">
          <rect x="1.5" y="3.5" width="13" height="9.5" rx="1" fill="#29a8e0"/>
          <path d="M1.8 4l6.2 4.8L14.2 4" fill="none" stroke="#1f2940" stroke-width="1.2"/>
        </svg>
        <span>hello@calderhealth.com</span>
      </li>
      <li class="contact-item">
        <svg class="contact-icon" viewBox="0 0 16 16" aria-hidden="true">
          <circle cx="8" cy="8" r="7" fill="#29a8e0"/>
          <path d="M1.5 8h13M8 1a10 10 0 0 1 0 14M8 1a10 10 0 0 0 0 14" fill="none" stroke="#1f2940" stroke-width="1"/>
        </svg>
        <span>www.calderhealth.com</span>
      </li>
    </ul>
    <div class="front-band"></div>
  </section>

  <section class="card card-back" aria-label="Card back">
    <div class="back-brand">
      <div class="back-ring"></div>
      <div class="back-name">Calder Health Partners</div>
    </div>
  </section>
</main>
</body>
</html>
```